Ridge Lass Crew (Flyer)

I want a flyer to advertise my service.
Details below, and logo's to use are attached.

A girls only after school program, 11-14yrs, as OSHC is no longer avail, dedicated to coaching & mentoring our girls into strong, independent young women.

The Brainchild of Rebecca Folwin, Ridge Lass Crew was created to address the growing demand for after school/school holiday supervision for kids moving from primary into high school, when OSHC ceases to exist.
With over 12 years experience mentoring and coaching young women in the corporate world, Bec decided to leave her role as a Director with Tarrant Trust, and follow her passion.
Bec, along with her sister Lorraine, who has over 10 years experience in local communities as a Youth Worker, and is also a qualified Enrolled Nurse, embarked on building a program designed to keep parents happy (by knowing their girls are safe) and dedicated to coaching and mentoring our girls into strong, independent young women.
Open every afternoon and during school holidays, we look to offer;
- Daily meditation
- Healthy snacks
- Dedicated homework time
- Organised group activity, led by qualified instructors (yoga, fitness class, soccer etc)
- Regular guests speakers, addressing issues/concerns for young people today
- SOCIAL MEDIA FREE ZONE

Located 87 Pelham Pde, Larkfield Heights (across from Crestmoor Day Clinic)
Open 3-6pm Monday to Friday

Facebook page: http://fb.example/ridgelasscrew
Email: info@ridgelasscrew.example.au
Mobile: 0455817396

Target Market(s)

Parents of teenage girls, teenage girls 11-14 years

Industry/Entity Type

School

Font styles to use
Sans Serif

Colors
b768aa
e667a6

Requirements
Must have
• What progam is - see brief
• Who runs it
Should not have
• Not be too busy, not overly mature images

```html
<!DOCTYPE html>
<html lang="en">
<head>
<meta charset="utf-8">
<title>Ridge Lass Crew – After School Program Flyer</title>
<link rel="stylesheet" href="https://fonts.googleapis.com/css2?family=Rubik+Dirt&family=Overlock:wght@700;900&family=Marcellus+SC&family=Marcellus&family=Lora:ital@1&family=Open+Sans:wght@700&family=PT+Sans+Narrow&display=swap">
<style>
  :root {
    --mauve: #b768aa;
    --magenta: #c51fb8;
    --magenta-dark: #8e1487;
    --pink: #e667a6;
    --pink-soft: #e87bb2;
    --white: #ffffff;
    --ink: #1c1420;
    --ink-soft: #3a3340;
    --ring: #d9d6da;
  }
  * { box-sizing: border-box; margin: 0; padding: 0; }
  html, body { width: 927px; height: 1200px; overflow: hidden; background: var(--mauve); }
  .flyer { position: relative; width: 927px; height: 1200px; background: var(--mauve); overflow: hidden; }

  .hero-band {
    position: absolute; left: 0; top: 72px; width: 927px; height: 440px;
    background: radial-gradient(circle at 70% 45%, #d42fcb 0%, var(--magenta) 45%, var(--magenta-dark) 100%);
  }
  .hero-word {
    position: absolute; font-family: "Rubik Dirt", sans-serif; color: var(--white);
    letter-spacing: 3px; line-height: 1;
  }
  .hero-word.teamwork { left: 318px; top: 92px; font-size: 62px; }
  .hero-word.support { left: 488px; top: 180px; font-size: 78px; }
  .hero-word.strategy { left: 420px; top: 300px; font-size: 70px; }
  .hero-word.goals { left: 512px; top: 388px; font-size: 86px; }

  .face-photo {
    position: absolute; left: 0; top: 208px; width: 152px; height: 304px;
    background: linear-gradient(160deg, #9fd04a 0%, #6fa82c 55%, #3b3f2a 100%);
  }

  .brand-box {
    position: absolute; left: 18px; top: 20px; width: 266px; height: 312px;
    background: var(--white);
    display: flex; align-items: center; justify-content: center; text-align: center;
  }
  .brand-name {
    font-family: "Overlock", sans-serif; font-weight: 900; color: var(--pink);
    font-size: 54px; line-height: 1.02;
  }

  .activity-photo {
    position: absolute; top: 336px; width: 200px; height: 200px; border-radius: 50%;
    border: 7px solid var(--ring);
  }
  .activity-photo.dance { left: 144px; background: linear-gradient(135deg, #e9e1d6, #b8a99a 60%, #2c2b3a); }
  .activity-photo.soccer { left: 364px; background: linear-gradient(160deg, #3f4a5a 0%, #c4242c 55%, #e3dedc 100%); }
  .activity-photo.meditate { left: 580px; background: linear-gradient(180deg, #9fc3e0 0%, #4b86b4 35%, #d9c9a8 70%, #c8b48d 100%); }

  .program-banner {
    position: absolute; left: 102px; top: 540px; width: 730px; height: 114px;
    background: var(--pink-soft); border-radius: 8px; text-align: center; color: var(--white);
  }
  .program-title { font-family: "Overlock", sans-serif; font-weight: 900; font-size: 43px; margin-top: 4px; line-height: 1.1; }
  .program-age { font-family: "Open Sans", sans-serif; font-weight: 700; font-size: 42px; line-height: 1.1; }
  .program-age small { font-size: 21px; margin-left: 10px; }

  .founder { position: absolute; left: 0; top: 700px; width: 927px; text-align: center;
    font-family: "Marcellus SC", serif; color: var(--ink); font-size: 38px; line-height: 42px; letter-spacing: 2px; }

  .offer-heading { position: absolute; left: 48px; top: 818px; font-family: "Overlock", sans-serif;
    font-weight: 700; color: var(--white); font-size: 38px; line-height: 1.2; }

  .offer-row { position: absolute; display: flex; gap: 30px; font-family: "Lora", serif; font-style: italic;
    color: var(--white); font-size: 26px; letter-spacing: 0.6px; white-space: nowrap; line-height: 32px; }
  .offer-row.r1 { left: 30px; top: 874px; }
  .offer-row.r2 { left: 64px; top: 920px; }
  .offer-row.r3 { left: 108px; top: 966px; }
  .offer-item { display: flex; align-items: center; gap: 12px; }
  .offer-item svg { width: 16px; height: 16px; flex: none; }

  .hours { position: absolute; left: 0; top: 1018px; width: 927px; text-align: center; }
  .hours-main { font-family: "Marcellus", serif; color: var(--ink); font-size: 35px; line-height: 40px; }
  .hours-time { font-family: "Open Sans", sans-serif; font-weight: 700; color: var(--ink-soft); font-size: 25px;
    line-height: 28px; text-shadow: 1px 1px 1px rgba(255,255,255,0.4); }

  .contact-bar { position: absolute; left: 6px; top: 1106px; width: 916px; height: 90px; background: var(--pink-soft);
    border-radius: 6px; font-family: "PT Sans Narrow", sans-serif; color: var(--ink); font-size: 20px; line-height: 1.3; }
  .contact-icon { position: absolute; width: 34px; height: 34px; border-radius: 50%; background: var(--mauve);
    display: flex; align-items: center; justify-content: center; }
  .contact-text { position: absolute; }
  .contact-text small { font-size: 15px; }
</style>
</head>
<body>
<main class="flyer">
  <div class="hero-band" role="img" aria-label="Magenta background with a white web of radiating lines"></div>
  <div class="hero-word teamwork">TEAMWORK</div>
  <div class="hero-word support">SUPPORT</div>
  <div class="hero-word strategy">STRATEGY</div>
  <div class="hero-word goals">GOALS</div>

  <div class="face-photo" role="img" aria-label="Photo of a smiling girl tinted green"></div>

  <div class="brand-box"><div class="brand-name">Ridge<br>Lass<br>Crew</div></div>

  <div class="activity-photo dance" role="img" aria-label="Photo of two women stretching in a dance pose"></div>
  <div class="activity-photo soccer" role="img" aria-label="Photo of a girls soccer team in red jerseys with their coach"></div>
  <div class="activity-photo meditate" role="img" aria-label="Photo of a girl meditating on a beach dune"></div>

  <section class="program-banner">
    <div class="program-title">A Girls Only After School Program</div>
    <div class="program-age">11-14yrs<small>as OSHC is no longer available</small></div>
  </section>

  <div class="founder">The Brainchild of Rebecca Folwin<br>Ridge Lass Crew</div>

  <h2 class="offer-heading">We look to offer</h2>
  <div class="offer-row r1">
    <span class="offer-item"><svg viewBox="0 0 16 16"><circle cx="8" cy="8" r="6.5" fill="none" stroke="#fff" stroke-width="1.6"/><path d="M5 8.2l2 2 4-4" fill="none" stroke="#fff" stroke-width="1.6"/></svg>Daily meditation</span>
    <span class="offer-item"><svg viewBox="0 0 16 16"><circle cx="8" cy="8" r="6.5" fill="none" stroke="#fff" stroke-width="1.6"/><path d="M5 8.2l2 2 4-4" fill="none" stroke="#fff" stroke-width="1.6"/></svg>Healthy snacks</span>
    <span class="offer-item"><svg viewBox="0 0 16 16"><circle cx="8" cy="8" r="6.5" fill="none" stroke="#fff" stroke-width="1.6"/><path d="M5 8.2l2 2 4-4" fill="none" stroke="#fff" stroke-width="1.6"/></svg>Dedicated homework time</span>
  </div>
  <div class="offer-row r2">
    <span class="offer-item"><svg viewBox="0 0 16 16"><circle cx="8" cy="8" r="6.5" fill="none" stroke="#fff" stroke-width="1.6"/><path d="M5 8.2l2 2 4-4" fill="none" stroke="#fff" stroke-width="1.6"/></svg>Organised group activity, (yoga, fitness class, soccer etc.)</span>
  </div>
  <div class="offer-row r3">
    <span class="offer-item"><svg viewBox="0 0 16 16"><circle cx="8" cy="8" r="6.5" fill="none" stroke="#fff" stroke-width="1.6"/><path d="M5 8.2l2 2 4-4" fill="none" stroke="#fff" stroke-width="1.6"/></svg>Regular guests speakers</span>
    <span class="offer-item"><svg viewBox="0 0 16 16"><circle cx="8" cy="8" r="6.5" fill="none" stroke="#fff" stroke-width="1.6"/><path d="M5 8.2l2 2 4-4" fill="none" stroke="#fff" stroke-width="1.6"/></svg>Social media free zone</span>
  </div>

  <div class="hours">
    <div class="hours-main">Open every afternoon and during school holidays</div>
    <div class="hours-time">3-6pm Monday to Friday</div>
  </div>

  <footer class="contact-bar">
    <div class="contact-icon" style="left:8px;top:8px;">
      <svg width="20" height="16" viewBox="0 0 20 16"><rect x="1" y="1" width="18" height="14" rx="2" fill="#fff"/><path d="M2 2l8 7 8-7" fill="none" stroke="#b768aa" stroke-width="1.6"/></svg>
    </div>
    <div class="contact-icon" style="left:16px;top:56px;width:26px;height:26px;"></div>
    <div class="contact-text" style="left:70px;top:0px;">e-Mail us<br>info@ridgelasscrew.example.au</div>
    <div class="contact-text" style="left:64px;top:62px;font-size:18px;">http://fb.example/ridgelasscrew</div>

    <div class="contact-icon" style="left:384px;top:22px;">
      <svg width="14" height="22" viewBox="0 0 14 22"><rect x="1" y="1" width="12" height="20" rx="2.5" fill="#fff"/><rect x="3" y="4" width="8" height="12" fill="#b768aa"/><circle cx="7" cy="18.5" r="1.2" fill="#b768aa"/></svg>
    </div>
    <div class="contact-text" style="left:418px;top:14px;">Call Us Now<br><b>0455817396</b></div>

    <div class="contact-icon" style="left:664px;top:10px;">
      <svg width="16" height="22" viewBox="0 0 16 22"><path d="M8 1a7 7 0 0 1 7 7c0 5-7 13-7 13S1 13 1 8a7 7 0 0 1 7-7z" fill="#fff"/><circle cx="8" cy="8" r="2.6" fill="#b768aa"/></svg>
    </div>
    <div class="contact-text" style="left:702px;top:6px;">87 Pelham Pde,<br>Larkfield Heights<br><small>(across from Crestmoor Day Clinic)</small></div>
  </footer>
</main>
</body>
</html>
```